Business Card Design Project

I need a business card designed from scratch. I have an existing logo that I can upload in Illustrator for modification or redesign.

The Company is called Query Lanterns http://querylanterns.com.au and we provide Search Engine Optimization services to Australian businesses. The current logo signifies an increase in visitors, profits etc...

There are no restrictions as to the redesign - colours, style etc are all open to change.

Cards will be full colour and one sided printed at http://www.cardmoxel.com.au so check their requirements for file format and sizes etc.

I will expect all original files upon completion of project.

Target Market(s)

Any business with a web site looking to improve their search engine rankings

Industry/Entity Type

Business

Requirements
Must have
• I like modern, sleek designs. Clean, not fussy, uncluttered.

```html
<!DOCTYPE html>
<html lang="en">
<head>
<meta charset="utf-8">
<title>Query Lanterns – Business Cards</title>
<link rel="stylesheet" href="https://fonts.googleapis.com/css2?family=Source+Sans+3:wght@400;600;700&display=swap">
<style>
  :root {
    --stage: #a9821f;
    --card-white: #ffffff;
    --card-grey: #e9e9e9;
    --brand-blue: #1f6fb5;
    --brand-yellow: #f5c518;
    --ink: #2a2a2a;
    --divider: #9a9a9a;
    --orange-edge: #fb9a06;
    --orange-mid: #fbb21a;
    --orange-core: #f2dc3c;
  }
  * { box-sizing: border-box; margin: 0; padding: 0; }
  html, body {
    width: 1200px;
    height: 686px;
    overflow: hidden;
  }
  body {
    position: relative;
    background: var(--stage);
    font-family: "Source Sans 3", "Myriad Pro", Arial, sans-serif;
    color: var(--ink);
  }
  .card {
    position: absolute;
    width: 508px;
    height: 288px;
    border-radius: 26px;
    overflow: hidden;
  }
  .card--front {
    left: 69px; top: 49px;
    background: radial-gradient(ellipse at 50% 45%, var(--card-white) 0%, var(--card-grey) 100%);
  }
  .card--back-light {
    left: 613px; top: 49px;
    background: radial-gradient(ellipse at 50% 45%, var(--card-white) 0%, var(--card-grey) 100%);
  }
  .card--back-orange {
    left: 406px; top: 362px;
    height: 290px;
    background: radial-gradient(ellipse at 50% 45%, var(--orange-core) 0%, var(--orange-mid) 45%, var(--orange-edge) 100%);
  }

  /* front: brand block */
  .brand {
    position: absolute;
    left: 16px; top: 122px;
    display: flex;
    align-items: center;
    gap: 8px;
  }
  .brand__dot {
    width: 14px; height: 14px;
    border-radius: 50%;
    background: var(--brand-yellow);
    flex: none;
  }
  .brand__name {
    font-weight: 700;
    font-size: 27px;
    line-height: 1;
    color: var(--brand-blue);
    white-space: nowrap;
  }
  .divider {
    position: absolute;
    left: 249px; top: 101px;
    width: 1px; height: 84px;
    background: linear-gradient(to bottom, transparent, var(--divider) 20%, var(--divider) 80%, transparent);
  }

  /* front: contact block */
  .contact {
    position: absolute;
    left: 263px; top: 86px;
  }
  .contact__heading {
    display: flex;
    align-items: center;
    gap: 8px;
    height: 22px;
  }
  .contact__name {
    font-weight: 700;
    font-size: 18px;
    color: var(--brand-blue);
  }
  .contact__sep {
    width: 1px; height: 14px;
    background: var(--brand-blue);
  }
  .contact__title {
    font-weight: 700;
    font-size: 13px;
    color: var(--brand-yellow);
  }
  .contact__list {
    list-style: none;
    margin-top: 8px;
  }
  .contact__item {
    display: flex;
    align-items: center;
    gap: 5px;
    font-size: 12.5px;
    height: 17.5px;
  }
  .contact__icon {
    width: 10px; height: 10px;
    flex: none;
    fill: var(--brand-blue);
  }
  .contact__address {
    margin-top: 9px;
    margin-left: 2px;
    font-size: 12.5px;
  }

  /* back sides: brand name as centred wordmark */
  .back-name {
    position: absolute;
    inset: 0;
    display: flex;
    align-items: center;
    justify-content: center;
    gap: 12px;
  }
  .back-name__dot {
    width: 20px; height: 20px;
    border-radius: 50%;
    background: var(--brand-yellow);
  }
  .card--back-orange .back-name__dot { background: var(--card-white); }
  .back-name__text {
    font-weight: 700;
    font-size: 40px;
    color: var(--brand-blue);
  }
</style>
</head>
<body>

  <section class="card card--front" aria-label="Card front">
    <div class="brand">
      <span class="brand__dot"></span>
      <span class="brand__name">Query Lanterns</span>
    </div>
    <div class="divider"></div>
    <div class="contact">
      <div class="contact__heading">
        <span class="contact__name">Your Name</span>
        <span class="contact__sep"></span>
        <span class="contact__title">Title</span>
      </div>
      <ul class="contact__list">
        <li class="contact__item">
          <svg class="contact__icon" viewBox="0 0 10 10" aria-hidden="true"><path d="M2 0.5 L3.6 0.5 L4.2 3 L3 3.8 Q4 6.2 6.2 7 L7 5.8 L9.5 6.4 L9.5 8 Q9.5 9.5 8 9.5 Q1 9 0.5 2 Q0.5 0.5 2 0.5Z"/></svg>
          123-456-7890
        </li>
        <li class="contact__item">
          <svg class="contact__icon" viewBox="0 0 10 10" aria-hidden="true"><path d="M0 2 H10 V8.5 H0Z M0.6 2.4 L5 5.6 L9.4 2.4" stroke="#fff" stroke-width="0.8"/></svg>
          inquiry@querylanterns.com.au.com
        </li>
        <li class="contact__item">
          <svg class="contact__icon" viewBox="0 0 10 10" aria-hidden="true"><circle cx="5" cy="5" r="4.8"/><path d="M0.4 5 H9.6 M5 0.3 V9.7 M1.3 2.8 H8.7 M1.3 7.2 H8.7" stroke="#fff" stroke-width="0.6" fill="none"/><ellipse cx="5" cy="5" rx="2" ry="4.6" stroke="#fff" stroke-width="0.6" fill="none"/></svg>
          www.querylanterns.com.au
        </li>
      </ul>
      <p class="contact__address">Street name City, State, zip code</p>
    </div>
  </section>

  <section class="card card--back-light" aria-label="Card back, light version">
    <div class="back-name">
      <span class="back-name__dot"></span>
      <span class="back-name__text">Query Lanterns</span>
    </div>
  </section>

  <section class="card card--back-orange" aria-label="Card back, orange version">
    <div class="back-name">
      <span class="back-name__dot"></span>
      <span class="back-name__text">Query Lanterns</span>
    </div>
  </section>

</body>
</html>
```